Laser Tattoo Removal Business Cards

We are looking for a professional business card design for a laser tattoo removal business. Ideally looking for a black business card design. The name of the business is Brightline Tattoo Removal. We place our cards at local tattoo shops so we ideally are looking for something trendy/edgy to draw both male and female clientele in.

Target Market(s)

Male/Female ages 18-60

Contact Information for Business Card

black background ideally.. hoping to stay within greys, whites and black

Font styles to use
Serif
Sans Serif

Colors
121212
a9a9a9
5c5c5c
f5f5f5
ffffff
7f7f7f
606060
848484
9d9d9d

Requirements
Must have
• Employee Info:
• Melissa Thornbury
• Chief Executive Offer
• m: 919.537.2846
• w: 919.362.4178
• f: 919.685.3907
• mthornbury@brightlinetattooremoval.example
• Address:
• 4615 Oakmere Pkwy, Suite 210
• Raleigh, NC 27654
• Website:
• www.brightlinetattooremoval.example
Nice to have
• Myabe business name on back or logo on back and employee info on the front

```html
<!DOCTYPE html>
<html lang="en">
<head>
<meta charset="utf-8">
<title>Brightline Tattoo Removal – Business Cards</title>
<link rel="stylesheet" href="https://fonts.googleapis.com/css2?family=Oswald:wght@300;400&family=Mulish:wght@400;700&display=swap">
<style>
  :root {
    --backdrop: #a9a9a9;
    --card-light: #ffffff;
    --card-dark: #1c1d1e;
    --ink: #121212;
    --ink-soft: #5c5c5c;
    --ink-muted: #9d9d9d;
    --rule-dark: #7f7f7f;
    --brand: #f5f5f5;
  }
  * { box-sizing: border-box; margin: 0; padding: 0; }
  html, body { width: 1200px; height: 960px; overflow: hidden; }
  body { background: var(--backdrop); position: relative; font-family: "Mulish", sans-serif; }

  .card-back {
    position: absolute; left: 511px; top: 309px; width: 521px; height: 343px;
    background: var(--card-dark);
  }
  .card-back__frame {
    position: absolute; left: 7px; top: 9px; right: 10px; bottom: 11px;
    border: 1px solid var(--rule-dark);
  }
  .brand-name {
    position: absolute; left: 0; right: 0; top: 112px;
    text-align: center;
    font-family: "Oswald", sans-serif; font-weight: 400;
    font-size: 36px; line-height: 48px; letter-spacing: 5px;
    text-transform: uppercase; color: var(--brand);
  }

  .card-front {
    position: absolute; left: 168px; top: 180px; width: 343px; height: 600px;
    background: var(--card-light);
  }
  .card-front__frame {
    position: absolute; left: 10px; top: 8px; right: 10px; bottom: 11px;
    border: 1px solid var(--ink);
  }
  .contact-item { position: absolute; left: 0; right: 0; text-align: center; }
  .icon {
    display: block; margin: 0 auto; width: 29px; height: 29px;
  }
  .person-name {
    font-family: "Oswald", sans-serif; font-weight: 400;
    font-size: 40px; line-height: 44px; color: var(--ink);
    transform: scaleX(0.86); letter-spacing: 0.5px; margin-top: 6px;
  }
  .person-title {
    font-weight: 700; font-size: 12.5px; letter-spacing: 0.4px;
    color: var(--ink-muted); text-transform: uppercase; margin-top: -2px;
  }
  .contact-text {
    font-size: 14px; line-height: 18px; color: var(--ink-soft); margin-top: 11px;
  }
</style>
</head>
<body>

<section class="card-back" aria-label="Card back">
  <div class="card-back__frame"></div>
  <p class="brand-name">Brightline<br>Tattoo Removal</p>
</section>

<section class="card-front" aria-label="Card front">
  <div class="card-front__frame"></div>

  <div class="contact-item" style="top:34px">
    <svg class="icon" viewBox="0 0 30 30" aria-hidden="true">
      <circle cx="15" cy="15" r="14" fill="none" stroke="#121212" stroke-width="1"/>
      <circle cx="15" cy="11.5" r="4" fill="#121212"/>
      <path d="M7.5 21.5c0-4 3.5-5.5 7.5-5.5s7.5 1.5 7.5 5.5z" fill="#121212"/>
    </svg>
    <h1 class="person-name">MELISSA THORNBURY</h1>
    <p class="person-title">Chief Executive Offer</p>
  </div>

  <div class="contact-item" style="top:143px">
    <svg class="icon" viewBox="0 0 30 30" aria-hidden="true">
      <circle cx="15" cy="15" r="14" fill="none" stroke="#121212" stroke-width="1"/>
      <path d="M15 7a5 5 0 0 0-5 5c0 4 5 10 5 10s5-6 5-10a5 5 0 0 0-5-5z" fill="#121212"/>
      <circle cx="15" cy="12" r="1.8" fill="#fff"/>
    </svg>
    <p class="contact-text">4615 Oakmere Pkwy, Suite 210<br>Raleigh, NC 27654</p>
  </div>

  <div class="contact-item" style="top:236px">
    <svg class="icon" viewBox="0 0 30 30" aria-hidden="true">
      <circle cx="15" cy="15" r="14" fill="none" stroke="#121212" stroke-width="1"/>
      <path d="M10.5 8.5l2.5-.5 1.5 3.5-1.8 1.2c.8 1.8 2.2 3.2 4 4l1.2-1.8 3.5 1.5-.5 2.5c-5.5.5-11-5-10.4-10.4z" fill="#121212"/>
    </svg>
    <p class="contact-text">919.362.4178</p>
  </div>

  <div class="contact-item" style="top:302px">
    <svg class="icon" viewBox="0 0 30 30" aria-hidden="true">
      <circle cx="15" cy="15" r="14" fill="none" stroke="#121212" stroke-width="1"/>
      <rect x="11" y="7.5" width="8" height="15" rx="1.5" fill="#121212"/>
      <rect x="12.3" y="9.5" width="5.4" height="9.5" fill="#fff"/>
    </svg>
    <p class="contact-text">919.537.2846</p>
  </div>

  <div class="contact-item" style="top:367px">
    <svg class="icon" viewBox="0 0 30 30" aria-hidden="true">
      <circle cx="15" cy="15" r="14" fill="none" stroke="#121212" stroke-width="1"/>
      <rect x="11" y="8" width="8" height="5" fill="#121212"/>
      <rect x="8" y="13" width="14" height="6" rx="1" fill="#121212"/>
      <rect x="11" y="17" width="8" height="5" fill="#121212" stroke="#fff" stroke-width="1"/>
    </svg>
    <p class="contact-text">919.685.3907</p>
  </div>

  <div class="contact-item" style="top:433px">
    <svg class="icon" viewBox="0 0 30 30" aria-hidden="true">
      <circle cx="15" cy="15" r="14" fill="none" stroke="#121212" stroke-width="1"/>
      <rect x="9" y="10.5" width="12" height="9" fill="#121212"/>
      <path d="M9 10.5l6 5 6-5" fill="none" stroke="#fff" stroke-width="1"/>
    </svg>
    <p class="contact-text">mthornbury@brightlinetattooremoval.example</p>
  </div>

  <div class="contact-item" style="top:498px">
    <svg class="icon" viewBox="0 0 30 30" aria-hidden="true">
      <circle cx="15" cy="15" r="14" fill="none" stroke="#121212" stroke-width="1"/>
      <circle cx="15" cy="15" r="6.5" fill="#121212"/>
      <path d="M11 12.5c1.5 0 2 1.5 3 2s1 2 0 3M17.5 10.5c-1 1 0 2 1.5 2.5" fill="none" stroke="#fff" stroke-width="1.1"/>
    </svg>
    <p class="contact-text">www.brightlinetattooremoval.example</p>
  </div>
</section>

</body>
</html>
```